Gobal construction supply company needs new business card design

I need a business card design for my global supply company using an existing logo. i will be looking to print these on rounded corner cards with the black background version of my logo on the back. on the front white background, my logo again and my simple details.

```html
<!DOCTYPE html>
<html lang="en">
<head>
<meta charset="utf-8">
<title>Meridian Build Supply – Business Card</title>
<link rel="stylesheet" href="https://fonts.googleapis.com/css2?family=Roboto:wght@400;700;900&display=swap">
<style>
  :root {
    --backdrop: #3a3a3a;
    --ink-black: #000000;
    --card-dark: #1b1b1b;
    --paper: #f2f2f2;
    --brand-red: #dd0000;
    --text-dark: #111111;
    --text-body: #555555;
    --white: #ffffff;
    --hatch-tone: #8a8a8a;
  }
  * { margin: 0; padding: 0; box-sizing: border-box; }
  html, body { width: 1200px; height: 960px; overflow: hidden; }
  body {
    background: var(--backdrop);
    font-family: "Roboto", Arial, sans-serif;
    position: relative;
  }

  .card {
    position: absolute;
    width: 600px;
    height: 343px;
    border-radius: 20px;
    overflow: hidden;
    box-shadow: 0 6px 14px rgba(0,0,0,.45);
  }

  /* Front */
  .card--front { left: 186px; top: 113px; background: var(--paper); }
  .front__brand-panel {
    position: absolute; left: 0; top: 0; width: 263px; height: 100%;
    background: var(--ink-black);
    display: flex; flex-direction: column; align-items: center; justify-content: center;
    gap: 10px;
  }
  .brand-name {
    color: var(--white); font-weight: 700; text-transform: uppercase;
    display: flex; align-items: center; gap: 8px;
  }
  .brand-name--small { font-size: 17px; letter-spacing: .3px; }
  .brand-dot { background: var(--brand-red); border-radius: 50%; flex: none; }
  .brand-dot--small { width: 12px; height: 12px; }
  .front__divider {
    position: absolute; left: 263px; top: 0; width: 12px; height: 100%;
    background: var(--brand-red);
  }
  .front__divider-hatch {
    position: absolute; left: 265px; top: 62px; width: 10px; height: 220px;
    background: var(--hatch-tone);
  }

  .contact { position: absolute; left: 292px; top: 66px; }
  .contact__row { display: flex; align-items: flex-start; gap: 13px; }
  .contact__row + .contact__row { margin-top: 18px; }
  .contact__icon {
    width: 22px; height: 22px; background: var(--brand-red); flex: none;
    display: flex; align-items: center; justify-content: center; margin-top: 2px;
  }
  .contact__name { font-size: 21px; font-weight: 700; color: var(--text-dark); line-height: 1; margin-top: 1px; }
  .contact__role { font-size: 14px; font-weight: 700; color: var(--brand-red); margin-top: 4px; }
  .contact__text { font-size: 14px; color: var(--text-body); line-height: 19px; }
  .contact__row--name + .contact__row { margin-top: 24px; }

  /* Back */
  .card--back { left: 434px; top: 511px; background: var(--card-dark); }
  .back__brand {
    position: absolute; left: 0; right: 0; top: 100px;
    display: flex; justify-content: center;
  }
  .brand-name--large { font-size: 44px; font-weight: 900; letter-spacing: 1px; gap: 16px; }
  .brand-dot--large { width: 36px; height: 36px; align-self: flex-start; }
  .back__tab { position: absolute; top: 293px; height: 18px; background: var(--brand-red); }
  .back__tab--left { left: 0; width: 100px; }
  .back__tab--right { right: 0; width: 102px; }
  .back__hatch { position: absolute; top: 293px; left: 104px; width: 390px; height: 16px; background: var(--hatch-tone); }
  .back__footer {
    position: absolute; left: 0; bottom: 0; width: 100%; height: 28px;
    background: var(--brand-red);
    color: var(--white); font-size: 14px; letter-spacing: 3.2px;
    display: flex; align-items: center; justify-content: center;
  }
</style>
</head>
<body>

<section class="card card--front" aria-label="Business card front">
  <div class="front__brand-panel">
    <div class="brand-name brand-name--small">Meridian Build Supply <span class="brand-dot brand-dot--small"></span></div>
  </div>
  <div class="front__divider"></div>
  <div class="front__divider-hatch" role="img" aria-label="Diagonal hazard stripe band"></div>

  <div class="contact">
    <div class="contact__row contact__row--name">
      <span class="contact__icon">
        <svg width="14" height="14" viewBox="0 0 14 14"><circle cx="7" cy="4.5" r="3" fill="#fff"/><path d="M1 14 Q1 8.5 7 8.5 Q13 8.5 13 14Z" fill="#fff"/></svg>
      </span>
      <div>
        <p class="contact__name">DANIEL CARTER</p>
        <p class="contact__role">CEO/FOUNDER</p>
      </div>
    </div>
    <div class="contact__row">
      <span class="contact__icon">
        <svg width="12" height="15" viewBox="0 0 12 15"><path d="M6 0.5A5 5 0 0 1 11 5.5C11 9 6 14.5 6 14.5S1 9 1 5.5A5 5 0 0 1 6 0.5Z" fill="#fff"/><circle cx="6" cy="5.5" r="2" fill="#dd0000"/></svg>
      </span>
      <p class="contact__text">2140 Harbor Ridge Road<br>Portland, Oregon 97210</p>
    </div>
    <div class="contact__row">
      <span class="contact__icon">
        <svg width="9" height="15" viewBox="0 0 9 15"><rect x="0.5" y="0.5" width="8" height="14" rx="1.5" fill="#fff"/><rect x="2" y="2.5" width="5" height="9" fill="#dd0000"/></svg>
      </span>
      <p class="contact__text">503 -218 -4471<br>503 -907 -3625</p>
    </div>
    <div class="contact__row">
      <span class="contact__icon">
        <svg width="14" height="10" viewBox="0 0 14 10"><rect width="14" height="10" fill="#fff"/><path d="M0 0 L7 6 L14 0" fill="none" stroke="#dd0000" stroke-width="1.3"/></svg>
      </span>
      <p class="contact__text">daniel@meridianbuild.com<br>www.meridianbuild.com</p>
    </div>
  </div>
</section>

<section class="card card--back" aria-label="Business card back">
  <div class="back__brand">
    <div class="brand-name brand-name--large">Meridian Build <span class="brand-dot brand-dot--large"></span></div>
  </div>
  <div class="back__tab back__tab--left"></div>
  <div class="back__hatch" role="img" aria-label="Diagonal hazard stripe band"></div>
  <div class="back__tab back__tab--right"></div>
  <div class="back__footer">www.meridianbuild.com</div>
</section>

</body>
</html>
```